Bright Harbor Web Design & Marketing

Will award a 2nd place prize of $100.00 if someone can come up with a logo to match this design!
Updates

Okay, I'm really looking to see some better designs here. What do you think will bring the best designs out? Please remember with all future submissions I'm looking for a cartoon style / illustrator style website. I'm not sure what the technical term is for it, so I uploaded some images in the brief.

Target Market(s)

Small Business Owners

Industry/Entity Type

Marketing

Logo Text

BrightHarbor.com

Number of Pages Required

1 page

Colors

Designer to choose colors to be used in the design.

Requirements
Must have
• Logo should say BrightHarbor.com I would like more than just a text logo. I want some sort of cool custom graphic / icon with it that will look nice on shirts/hats/etc

```html
<!DOCTYPE html>
<html lang="en">
<head>
<meta charset="utf-8">
<title>Bright Harbor Web Design &amp; Marketing</title>
<link href="https://fonts.googleapis.com/css2?family=Cinzel:wght@700&family=Open+Sans:wght@400;600;700;800&display=swap" rel="stylesheet">
<style>
:root{
  --orange:#f7931e;
  --navy:#15324f;
  --ink:#2b2b2b;
  --muted:#777;
  --header:#1d2630;
  --sky-top:#2f83d3;
  --sky-bottom:#a9d6f5;
  --dark-bg:#17232b;
  --band:#6e6f96;
  --light:#f3f3f1;
  --footer:#1d2126;
  --white:#fff;
}
*{box-sizing:border-box;margin:0;padding:0}
html,body{width:1200px;height:4736px;overflow:hidden}
body{font-family:"Open Sans",Arial,sans-serif;color:var(--ink);background:var(--white);position:relative}
section,header,footer{position:absolute;left:0;width:1200px}
.section-title{font-family:"Cinzel",Georgia,serif;font-size:34px;text-align:center;letter-spacing:1px;color:var(--ink)}
.section-title.light{color:var(--white)}
.section-intro{font-size:13px;line-height:1.7;text-align:center;color:var(--muted);width:760px;margin:14px auto 0}
.section-intro.light{color:#c9d1d6}
.btn{display:inline-block;font-size:14px;font-weight:600;padding:9px 18px;border-radius:3px;color:var(--white);white-space:nowrap}
.btn-orange{background:var(--orange)}
.btn-dark{background:#555}

.site-header{top:0;height:88px;background:var(--header);display:flex;align-items:center;justify-content:space-between;padding:0 60px}
.brand{display:flex;align-items:center;gap:12px;font-weight:800;font-size:26px;color:var(--white)}
.brand-dot{width:34px;height:34px;border-radius:50%;background:var(--orange)}
.main-nav{display:flex;height:88px}
.main-nav a{display:flex;align-items:flex-end;padding:0 18px 22px;font-size:13px;font-weight:700;color:var(--white);text-decoration:none}
.main-nav a.active{background:var(--orange)}

.hero{top:88px;height:412px;background:linear-gradient(180deg,var(--sky-top),var(--sky-bottom))}
.hero-art{position:absolute;left:60px;top:10px;width:460px;height:400px;background:linear-gradient(160deg,#4f7ea8,#2f4f70);border-radius:8px;opacity:.55}
.hero-copy{position:absolute;right:80px;top:80px;width:560px;text-align:right}
.hero-copy h1{font-size:44px;line-height:1.15;font-weight:800;color:var(--white)}
.hero-copy h1 span{color:var(--navy)}
.hero-copy .btn{margin-top:22px;background:#555}
.slide-arrow{position:absolute;top:190px;width:26px;height:34px;background:rgba(0,0,0,.45)}
.slide-arrow.prev{left:0}.slide-arrow.next{right:0}

.about{top:500px;height:300px;padding-top:52px;text-align:center}
.about .section-title span{color:var(--orange)}
.about .section-intro{width:860px}
.about-actions{margin-top:26px;display:flex;gap:12px;justify-content:center}

.services{top:800px;height:872px;background:radial-gradient(circle at 50% 55%,#2b3e48,var(--dark-bg) 70%);padding-top:40px}
.services svg{position:absolute;left:0;top:150px}

.pricing{top:1672px;height:668px;background:linear-gradient(180deg,#f7f7f7,#e2e2e2 80%);padding-top:48px}
.floor{position:absolute;left:0;bottom:0;width:1200px;height:110px;background:linear-gradient(180deg,#b27b48,#8a5630)}
.plans{position:absolute;top:130px;left:144px;display:flex;gap:24px;z-index:1}
.plan{width:210px;height:470px;background:var(--white);border-top:5px solid var(--orange);box-shadow:0 4px 14px rgba(0,0,0,.15);text-align:center;padding-top:26px}
.plan-icon{width:48px;height:48px;border-radius:50%;background:#2f83d3;margin:0 auto}
.plan h3{font-size:17px;font-weight:600;margin-top:16px}
.plan .from{font-size:11px;color:var(--muted);margin-top:14px}
.plan .price{font-size:36px;font-weight:700;color:var(--orange)}
.plan .price sup{font-size:16px}.plan .price small{font-size:14px}
.plan ul{list-style:none;text-align:left;margin:18px 0 0 30px;font-size:12px;color:var(--muted);line-height:2}
.plan li::before{content:"";display:inline-block;width:6px;height:6px;background:var(--orange);border-radius:50%;margin-right:8px;vertical-align:middle}
.plan-actions{display:flex;justify-content:space-between;align-items:center;padding:18px 16px 0}
.plan-actions .btn{font-size:11px;padding:6px 10px}
.plan-actions a:not(.btn){font-size:10px;color:var(--muted);white-space:nowrap}

.video{top:2340px;height:480px;padding-top:44px}
.video-art{position:absolute;left:380px;top:120px;width:440px;height:320px;background:linear-gradient(180deg,#7e82c4,#c9b59a);border-radius:14px}
.video-link{position:absolute;left:0;width:1200px;top:452px;text-align:center;font-size:12px;color:var(--orange)}
.tagline-band{top:2820px;height:120px;background:var(--band);display:flex;align-items:center;justify-content:center}
.tagline-band p{width:900px;text-align:center;font-family:"Cinzel",Georgia,serif;font-size:17px;line-height:1.6;color:var(--white)}

.clients{top:2940px;height:220px;background:var(--light);padding-top:40px}
.client-row{display:flex;justify-content:center;gap:30px;margin-top:26px}
.client{display:flex;align-items:center;gap:6px;font-size:15px;font-weight:700;color:#555}
.client i{width:12px;height:12px;background:#888;border-radius:50%}

.why{top:3160px;height:460px;background:linear-gradient(180deg,#1f2b22,#27341f);padding-top:40px}
.why svg{position:absolute;left:0;top:150px}

.team{top:3620px;height:420px;padding-top:52px}
.team-cards{display:flex;justify-content:center;gap:40px;margin-top:36px}
.member{width:440px;height:150px;border:1px solid #ddd;display:flex;gap:16px;padding:18px}
.member-photo{width:110px;height:110px;background:linear-gradient(160deg,#c7ccd2,#7d8894);flex:none}
.member h4{font-size:14px;font-weight:700}
.member .role{font-size:12px;color:var(--orange);margin-top:2px}
.member p{font-size:12px;line-height:1.6;color:var(--muted);margin-top:8px}
.team-arrow{position:absolute;top:250px;font-size:28px;color:#bbb}
.team-arrow.l{left:90px}.team-arrow.r{right:90px}

.inquiry{top:4040px;height:520px;background:linear-gradient(180deg,#fff,#eef0f2);padding-top:36px}
.inquiry-art{position:absolute;left:0;top:150px;width:300px;height:300px;background:linear-gradient(160deg,#dfe3e6,#a9b0b5)}
.inquiry-form{position:absolute;left:420px;top:120px;width:520px;display:grid;grid-template-columns:1fr 1fr;gap:14px 20px}
.field label{display:block;font-size:11px;color:var(--muted);margin-bottom:4px}
.field div{height:32px;border:1px solid #ccc;background:#fff}
.field.full{grid-column:1/3}
.field.full div{height:78px}
.inquiry-form .btn{width:90px;text-align:center;font-size:12px}

.site-footer{top:4560px;height:176px;background:linear-gradient(180deg,#2a3038,var(--footer));color:#cfd3d8}
.footer-cols{display:flex;gap:60px;padding:22px 0 0 70px}
.footer-cols h5{font-size:13px;color:var(--white);margin-bottom:8px}
.footer-cols h5 span{color:var(--orange)}
.footer-cols li{list-style:none;font-size:11px;line-height:1.7}
.footer-cols p{font-size:11px;line-height:1.7}
.news-input{width:200px;height:24px;background:#fff;margin-top:8px}
.news-btn{display:inline-block;margin-top:8px;font-size:11px;padding:4px 10px;background:#2f83d3;color:#fff}
.footer-mark{position:absolute;right:90px;top:26px;width:90px;height:90px;border-radius:50%;background:#3a424c}
.footer-bar{position:absolute;bottom:0;left:0;width:1200px;height:36px;background:#14171b;display:flex;justify-content:space-between;align-items:center;padding:0 70px;font-size:11px;color:#9aa0a6}
</style>
</head>
<body>

<header class="site-header">
  <div class="brand"><span class="brand-dot"></span>BrightHarbor.com</div>
  <nav class="main-nav">
    <a class="active">HOME</a><a>SERVICES &amp; PRICING</a><a>OUR TEAM</a><a>CLIENTS</a><a>CONTACT US</a>
  </nav>
</header>

<section class="hero">
  <div class="hero-art" role="img" aria-label="Cartoon illustration of a business team lifting a colleague into the air"></div>
  <span class="slide-arrow prev"></span><span class="slide-arrow next"></span>
  <div class="hero-copy">
    <h1>The Design &amp; Marketing<br>Team <span>That Always Puts</span><br>Bright Harbor <span>Before</span><br>Profits</h1>
    <a class="btn">Call Us Today</a>
  </div>
</section>

<section class="about">
  <h2 class="section-title">About <span>BrightHarbor.com</span></h2>
  <p class="section-intro">We believe that honesty and integrity come before personal profit. We are a family owned and operated studio that takes care of each client and their results just as we would our own. Our team is part of your business and we stay beside you every step of the way. We are working to grow hometown businesses with real results, fair pricing and long term partnerships.</p>
  <div class="about-actions"><a class="btn btn-orange">Read More</a><a class="btn btn-dark">Call Us Today</a></div>
</section>

<section class="services">
  <h2 class="section-title light">Services We Provide</h2>
  <p class="section-intro light">Every service below is built to help small business owners get found, win trust and grow steadily online with one dedicated team.</p>
  <svg width="1200" height="700" viewBox="0 0 1200 700" font-family="Open Sans, sans-serif">
    <g stroke="#8fa3ad" stroke-width="2">
      <line x1="600" y1="300" x2="430" y2="110"/><line x1="600" y1="300" x2="560" y2="70"/>
      <line x1="600" y1="300" x2="700" y2="100"/><line x1="600" y1="300" x2="790" y2="200"/>
      <line x1="600" y1="300" x2="810" y2="340"/><line x1="600" y1="300" x2="720" y2="480"/>
      <line x1="600" y1="300" x2="560" y2="500"/><line x1="600" y1="300" x2="410" y2="400"/>
      <line x1="600" y1="300" x2="380" y2="250"/>
    </g>
    <circle cx="600" cy="300" r="78" fill="#fff"/>
    <circle cx="600" cy="300" r="66" fill="#e9eef1"/>
    <circle cx="430" cy="110" r="36" fill="#f7931e"/>
    <circle cx="560" cy="70" r="30" fill="#8cc63f"/>
    <circle cx="700" cy="100" r="38" fill="#29abe2"/>
    <circle cx="790" cy="200" r="34" fill="#92278f"/>
    <circle cx="810" cy="340" r="30" fill="#ed1e79"/>
    <circle cx="720" cy="480" r="36" fill="#fbb03b"/>
    <circle cx="560" cy="500" r="32" fill="#2e8bd8"/>
    <circle cx="410" cy="400" r="38" fill="#39b54a"/>
    <circle cx="380" cy="250" r="34" fill="#c1272d"/>
    <g font-size="13" font-weight="700" fill="#f7931e">
      <text x="520" y="22" text-anchor="end">Company Review</text>
      <text x="750" y="80">Website Design &amp; Development</text>
      <text x="840" y="190">Logo Design &amp; Branding</text>
      <text x="855" y="335">Social Media Management</text>
      <text x="770" y="500">Pay Per Click Management</text>
      <text x="530" y="560">Search Engine Optimization</text>
      <text x="360" y="420" text-anchor="end">Marketing &amp; Print Design</text>
      <text x="330" y="250" text-anchor="end">Content Marketing</text>
      <text x="380" y="100" text-anchor="end">Email Marketing</text>
    </g>
    <g font-size="11" fill="#c9d1d6">
      <text x="520" y="40" text-anchor="end">Clear plans for your growth</text>
      <text x="750" y="98">Fast sites that convert</text>
      <text x="840" y="208">A look customers remember</text>
      <text x="855" y="353">Posts that build a following</text>
      <text x="770" y="518">Ads that pay for themselves</text>
      <text x="530" y="578">Rank higher on local search</text>
      <text x="360" y="438" text-anchor="end">Cards, flyers and signs</text>
      <text x="330" y="268" text-anchor="end">Articles that earn trust</text>
      <text x="380" y="118" text-anchor="end">Campaigns that bring people back</text>
    </g>
  </svg>
</section>

<section class="pricing">
  <h2 class="section-title">Select Your Plan</h2>
  <div class="floor"></div>
  <div class="plans">
    <div class="plan"><div class="plan-icon"></div><h3>Basic Plan</h3><p class="from">Starting From</p><p class="price"><sup>$</sup>52<small>.00</small></p>
      <ul><li>Simple Page Setup</li><li>Basic Site Hosting</li><li>One Logo Concept</li><li>Email Support Only</li><li>Monthly Site Check</li></ul>
      <div class="plan-actions"><a class="btn btn-orange">Get Started</a><a>More Information</a></div></div>
    <div class="plan"><div class="plan-icon"></div><h3>Standard Plan</h3><p class="from">Starting From</p><p class="price"><sup>$</sup>114<small>.00</small></p>
      <ul><li>Five Page Website</li><li>Fast Site Hosting</li><li>Two Logo Concepts</li><li>Phone And Email Help</li><li>Weekly Site Check</li></ul>
      <div class="plan-actions"><a class="btn btn-dark">Get Started</a><a>More Information</a></div></div>
    <div class="plan"><div class="plan-icon"></div><h3>Gold Plan</h3><p class="from">Starting From</p><p class="price"><sup>$</sup>200<small>.00</small></p>
      <ul><li>Ten Page Website</li><li>Local Search Setup</li><li>Full Brand Package</li><li>Priority Support</li><li>Monthly Report</li></ul>
      <div class="plan-actions"><a class="btn btn-dark">Get Started</a><a>More Information</a></div></div>
    <div class="plan"><div class="plan-icon"></div><h3>Platinum Plan</h3><p class="from">Starting From</p><p class="price"><sup>$</sup>490<small>.00</small></p>
      <ul><li>Unlimited Pages</li><li>Full Search Campaign</li><li>Social Media Care</li><li>Dedicated Manager</li><li>Weekly Report</li></ul>
      <div class="plan-actions"><a class="btn btn-dark">Get Started</a><a>More Information</a></div></div>
  </div>
</section>

<section class="video">
  <h2 class="section-title">Watch Video</h2>
  <div class="video-art" role="img" aria-label="Hands holding a tablet playing the company introduction video"></div>
  <p class="video-link">View Video</p>
</section>

<section class="tagline-band">
  <p>Lorem ipsum dolor sit amet, consectetur adipiscing elit, sed diam nonummy nibh euismod tincidunt ut laoreet dolore magna aliquam erat volutpat</p>
</section>

<section class="clients">
  <h2 class="section-title">Our Clients</h2>
  <p class="section-intro">Local shops, builders and service firms trust us to look after their online presence year after year.</p>
  <div class="client-row">
    <span class="client"><i></i>Northfield</span><span class="client">CORVALE</span><span class="client">CORVALE</span>
    <span class="client">Linden</span><span class="client"><i></i>Northfield</span><span class="client">Marlow</span>
    <span class="client">Westbay</span><span class="client">Westbay</span>
  </div>
</section>

<section class="why">
  <h2 class="section-title light">Why Choose Us</h2>
  <p class="section-intro light">We treat every client like a neighbor: honest advice, fair prices and work we are proud to sign our name to.</p>
  <svg width="1200" height="300" viewBox="0 0 1200 300" font-family="Open Sans, sans-serif">
    <g stroke="#8fa3ad" stroke-width="2" fill="none">
      <line x1="600" y1="130" x2="480" y2="60"/><line x1="600" y1="130" x2="460" y2="140"/><line x1="600" y1="130" x2="500" y2="220"/>
      <line x1="600" y1="130" x2="720" y2="60"/><line x1="600" y1="130" x2="740" y2="140"/><line x1="600" y1="130" x2="700" y2="220"/>
    </g>
    <circle cx="600" cy="130" r="60" fill="#fff"/><circle cx="600" cy="130" r="50" fill="#2e8bd8"/>
    <circle cx="480" cy="60" r="20" fill="#f7931e"/><circle cx="460" cy="140" r="20" fill="#2e8bd8"/><circle cx="500" cy="220" r="20" fill="#2e8bd8"/>
    <circle cx="720" cy="60" r="20" fill="#2e8bd8"/><circle cx="740" cy="140" r="20" fill="#2e8bd8"/><circle cx="700" cy="220" r="20" fill="#2e8bd8"/>
    <g font-size="13" font-weight="700" fill="#f7931e">
      <text x="450" y="55" text-anchor="end">Quality Results Guaranteed</text>
      <text x="430" y="135" text-anchor="end">Experienced Team</text>
      <text x="470" y="215" text-anchor="end">Affordable Pricing</text>
      <text x="750" y="55">Fast Turnaround</text>
      <text x="770" y="135">Ongoing Support</text>
      <text x="730" y="215">Transparent Reporting</text>
    </g>
    <g font-size="11" fill="#c9d1d6">
      <text x="450" y="72" text-anchor="end">We stand behind all our work</text>
      <text x="430" y="152" text-anchor="end">Years of small business projects</text>
      <text x="470" y="232" text-anchor="end">Plans for every budget</text>
      <text x="750" y="72">Projects delivered on time</text>
      <text x="770" y="152">Real people ready to help</text>
      <text x="730" y="232">Clear numbers every month</text>
    </g>
  </svg>
</section>

<section class="team">
  <h2 class="section-title">Our Team</h2>
  <p class="section-intro">Meet the people who answer your calls, build your site and keep your marketing on track.</p>
  <span class="team-arrow l">&#8249;</span><span class="team-arrow r">&#8250;</span>
  <div class="team-cards">
    <div class="member"><div class="member-photo" role="img" aria-label="Portrait photo of the chief executive officer"></div>
      <div><h4>MARCUS HALE</h4><p class="role">Chief Executive Officer</p><p>Marcus leads our studio and makes sure every client gets honest advice and work that brings real results.</p></div></div>
    <div class="member"><div class="member-photo" role="img" aria-label="Portrait photo of the chief operations officer"></div>
      <div><h4>OWEN FLETCHER</h4><p class="role">Chief Operations Officer</p><p>Owen keeps every project moving, from first call to launch day, so deadlines are always kept.</p></div></div>
  </div>
</section>

<section class="inquiry">
  <h2 class="section-title">Quick Inquiry</h2>
  <div class="inquiry-art" role="img" aria-label="Photo of hands typing on a laptop at a desk"></div>
  <div class="inquiry-form">
    <div class="field"><label>First Name</label><div></div></div>
    <div class="field"><label>Last Name</label><div></div></div>
    <div class="field"><label>Email</label><div></div></div>
    <div class="field"><label>Phone Number</label><div></div></div>
    <div class="field full"><label>Tell Us About Your Project</label><div></div></div>
    <a class="btn btn-orange">SUBMIT</a>
  </div>
</section>

<footer class="site-footer">
  <div class="footer-cols">
    <div><h5>Quick <span>Links</span></h5><ul><li>Home</li><li>Services</li><li>Pricing</li><li>Our Team</li><li>Contact</li></ul></div>
    <div><h5>Contact <span>Details</span></h5><p>Bright Harbor Studio<br>120 Harbor Lane, Suite 4<br>Portsmouth, NH 03801<br>(555) 014-2290<br>hello@brightharbor.com</p></div>
    <div><h5>Newsletter <span>Signup</span></h5><p>Get tips and offers each month.</p><div class="news-input"></div><span class="news-btn">Subscribe</span></div>
  </div>
  <div class="footer-mark"></div>
  <div class="footer-bar"><span>Copyright © 2017 BrightHarbor.com. All rights reserved.</span><span>Terms of Use | Privacy Policy</span></div>
</footer>

</body>
</html>
```